We’re a real estate firm that has landed a big builder in a neighboring state. Our branding needs...

We are a real estate firm who represents various builders along with doing resale here in Oregon. Our firm is growing to represent a big builder in Washington State and we’ll have another 40 brokers on our team. We need rebranding. As in, a new logo ( the house logo we have now looks cartoonish, hate it). We need new cards, something to really stand out. I’ve been thinking of using those NFC cards from ZEP or the ones with the seam color. I likely want two or three designs, a darker (as in a background color of black or grey) , a light one ( again I mean background color) and a credit card style (either plastic w an embossed name/number on front, or metal ). I’m thinking dark background for cc, or silver if it’s metal. That’s my thoughts, but you are the artists, so maybe you have an idea I haven’t considered. Our colors were black and red, but we don’t have to stick to that. Just nothing too busy. Oh, and we are typically representing the local, higher quality builders in our area (just below custom), but not national. Subdivisions are near the Kell Varney, Brisco, and Thornfield Crest sites. We are super excited, but without a lot of time to change the “look” of our brokerage. So I’ll be deciding and moving forward within 24 hours tops. Our name is Real Estate Summit Alliance ( we cant change the name because of timeline and business license) Thank you!

Industry/Entity Type

Real Estate

Contact Information for Business Card

The usual. Name of firm. Name of cardholder. Contact info.

Font styles to use
Serif
Sans Serif

Colors

Designer to choose colors to be used in the design.

Requirements
Must have
• A sleek or simple look. I included photos of cards with stylistic attributes we like. Thank you
Nice to have
• We really like the black backgrounds. With foil or embossed detail. We also like the black on black. Matte black card with raised shiny black detail. But still eye catching.
Should not have
• No ornate or busy looking style. We don’t want anything cluttered.

```html
<!DOCTYPE html>
<html lang="en">
<head>
<meta charset="utf-8">
<title>Real Estate Summit Alliance – Business Cards</title>
<link href="https://fonts.googleapis.com/css2?family=Open+Sans:wght@400;600&display=swap" rel="stylesheet">
<style>
  :root {
    --stage: #161617;
    --card: #1f1f20;
    --blue: #1566c8;
    --silver: #a9a9ab;
    --white: #f1f1f1;
    --rule: #4a4a4d;
  }
  * { margin: 0; padding: 0; box-sizing: border-box; }
  html, body {
    width: 1200px; height: 900px; overflow: hidden;
    background: var(--stage);
    font-family: "Open Sans", Arial, sans-serif;
  }
  .canvas { position: relative; width: 1200px; height: 900px; }
  .card {
    position: absolute;
    width: 560px; height: 320px;
    background: var(--card);
    border-radius: 22px;
    box-shadow: 0 18px 40px rgba(0,0,0,.55);
  }
  .card-back { left: 170px; top: 90px; }
  .card-front { left: 470px; top: 480px; }

  .back-name {
    position: absolute; left: 0; right: 0; top: 104px;
    text-align: center;
    font-weight: 600; font-size: 34px; line-height: 42px;
    color: var(--silver);
  }
  .back-web {
    position: absolute; left: 0; right: 0; top: 238px;
    text-align: center;
    font-size: 13px; letter-spacing: 1.5px; color: var(--white);
  }

  .brand-name {
    position: absolute; right: 36px; top: 44px; width: 250px;
    text-align: right;
    font-weight: 600; font-size: 26px; line-height: 32px;
    color: var(--blue);
  }
  .divider {
    position: absolute; left: 250px; right: 34px; top: 182px;
    height: 1px; background: var(--rule);
  }
  .holder { position: absolute; left: 36px; top: 188px; }
  .holder-name {
    color: var(--blue); font-weight: 600; font-size: 18px; letter-spacing: .5px;
    text-transform: uppercase;
  }
  .holder-role { color: var(--white); font-size: 15px; }
  .contacts { list-style: none; margin-top: 12px; }
  .contacts li {
    display: flex; align-items: center; gap: 8px;
    color: var(--white); font-size: 15px; line-height: 21px;
  }
  .contacts svg { width: 13px; height: 13px; fill: var(--blue); flex: none; }
  .address {
    position: absolute; right: 36px; top: 196px;
    text-align: right; color: var(--white); font-size: 14px; line-height: 20px;
    font-style: normal;
  }
</style>
</head>
<body>
<main class="canvas">
  <section class="card card-back" aria-label="Card back">
    <div class="back-name">Real Estate<br>Summit Alliance</div>
    <div class="back-web">WWW.SUMMITALLIANCE-RE.COM</div>
  </section>

  <section class="card card-front" aria-label="Card front">
    <div class="brand-name">Real Estate<br>Summit Alliance</div>
    <div class="divider"></div>

    <div class="holder">
      <div class="holder-name">Jonathan Smith</div>
      <div class="holder-role">Managing Director</div>
      <ul class="contacts">
        <li>
          <svg viewBox="0 0 16 16" aria-hidden="true"><path d="M2 5c0-2 2-3 6-3s6 1 6 3v1h-3V5H5v1H2zM4 7h8l2 7H2z"/></svg>
          044-123 456 789
        </li>
        <li>
          <svg viewBox="0 0 16 16" aria-hidden="true"><path d="M4 1h8v14H4zM5.5 3v9h5V3z"/></svg>
          044-123 456 789
        </li>
        <li>
          <svg viewBox="0 0 16 16" aria-hidden="true"><path d="M1 3h14v2L8 9 1 5zM1 7l7 4 7-4v6H1z"/></svg>
          info@summitalliance-re.com
        </li>
      </ul>
    </div>

    <address class="address">
      12345, Address Goes Here<br>
      Country Name, 123456
    </address>
  </section>
</main>
</body>
</html>
```